Heron Loan Partners Business Card

We need a business card design for our mortgage servicing company. In addition to servicing the loans of homeowners, we help homeowners with purchasing their homes and any mortgage refinancing. We would like to see designs that use the colors in the logo attached below (gold-ish yellow and navy blue), and any other design you deem fit! The design should communicate a simpler life with smart mortgages provided by Heron.

```html
<!DOCTYPE html>
<html lang="en">
<head>
<meta charset="utf-8">
<title>Heron Loan Partners Business Card</title>
<link href="https://fonts.googleapis.com/css2?family=Roboto:wght@400;700&display=swap" rel="stylesheet">
<style>
  :root {
    --navy: #231f55;
    --gold: #e3aa1f;
    --white: #ffffff;
    --backdrop: #2a2a2c;
    --ink-soft: #dcdcea;
  }
  * { box-sizing: border-box; margin: 0; padding: 0; }
  html, body { width: 1200px; height: 874px; overflow: hidden; }
  body {
    background: var(--backdrop);
    font-family: "Roboto", Arial, sans-serif;
    position: relative;
  }
  .card {
    position: absolute;
    width: 620px;
    height: 354px;
    border-radius: 22px;
    overflow: hidden;
    box-shadow: 0 14px 30px rgba(0,0,0,0.45);
  }
  .card--back {
    left: 480px; top: 60px;
    background: var(--navy);
    color: var(--white);
  }
  .card--front {
    left: 160px; top: 450px;
    background: var(--white);
  }
  .brand {
    position: absolute;
    left: 0; right: 0;
    display: flex;
    align-items: center;
    justify-content: center;
    gap: 14px;
  }
  .brand__mark {
    width: 18px; height: 18px;
    border-radius: 50%;
    background: var(--gold);
  }
  .brand__name {
    font-weight: 700;
    font-size: 40px;
    color: var(--gold);
    letter-spacing: 0.5px;
  }
  .card--back .brand { top: 120px; }
  .tagline {
    position: absolute;
    left: 0; right: 0; top: 248px;
    text-align: center;
    font-size: 17px;
    color: var(--white);
  }
  .card--front .brand { top: 70px; }
  .front__band {
    position: absolute;
    left: 0; right: 0; bottom: 0;
    height: 190px;
    background: var(--navy);
    border-top: 3px solid var(--gold);
  }
  .person {
    position: absolute;
    right: 330px; top: 196px;
    text-align: right;
    color: var(--white);
    font-size: 16px;
    line-height: 1.3;
  }
  .person__name {
    font-weight: 700;
    font-size: 25px;
    color: var(--gold);
    margin-bottom: 2px;
  }
  .divider {
    position: absolute;
    left: 308px; top: 204px;
    width: 1px; height: 100px;
    background: var(--ink-soft);
  }
  .contacts {
    position: absolute;
    left: 326px; top: 210px;
    list-style: none;
    color: var(--white);
    font-size: 16px;
  }
  .contacts li {
    display: flex;
    align-items: center;
    gap: 10px;
    height: 23px;
  }
  .contacts svg { width: 14px; height: 14px; fill: var(--gold); flex: none; }
</style>
</head>
<body>

<section class="card card--back">
  <div class="brand">
    <span class="brand__mark"></span>
    <span class="brand__name">Heron Loan Partners</span>
  </div>
  <p class="tagline">Simpler life with smart mortgages</p>
</section>

<section class="card card--front">
  <div class="brand">
    <span class="brand__mark"></span>
    <span class="brand__name">Heron Loan Partners</span>
  </div>
  <div class="front__band" role="img" aria-label="Navy band where a large brand silhouette with a gold outline sits"></div>

  <div class="person">
    <p class="person__name">Daniel Reyes</p>
    <p>President</p>
    <p>4120 Alder Court</p>
    <p>Fairview, Canada 58213</p>
  </div>

  <span class="divider"></span>

  <ul class="contacts">
    <li>
      <svg viewBox="0 0 16 16" aria-hidden="true"><path d="M3 1l3 3-2 2c1 2 3 4 5 5l2-2 3 3-2 3C6 15 1 10 1 3z"/></svg>
      555-214-7730
    </li>
    <li>
      <svg viewBox="0 0 16 16" aria-hidden="true"><path d="M4 0h8v16H4zM5.5 2v10h5V2z"/></svg>
      555-382-6105
    </li>
    <li>
      <svg viewBox="0 0 16 16" aria-hidden="true"><path d="M0 3h16v10H0zM1.5 4.5L8 9l6.5-4.5z"/></svg>
      hello@heronloanpartners.com
    </li>
    <li>
      <svg viewBox="0 0 16 16" aria-hidden="true"><circle cx="8" cy="8" r="7.5"/></svg>
      www.heronloanpartners.com
    </li>
  </ul>
</section>

</body>
</html>
```